Animal Eye Clinic needs a Business card

We are a new veterinary ophthalmology practice (Ridgeline Pet Vision Care) and we need a business card designed. We only see animal eyes - we are not a regular veterinary clinic. We already have a logo. We are looking for a professional, good looking business card to hand out to our clients. We are looking for something simple but professional and contemporary. Our logo is likely the only picture/graphic that needs to be on the card.
Updates

Contact Information for Business Card

Delia Vossman, BSc, DVM, MSc, DipACVO
Veterinary Ophthalmologist

Phone: 250.418.3927
Email: ridgelinepetvisioncare@mailbox-example.net
Website: ridgelinepetvisioncare-example.net
Address: 1874 Thornbury Rd
Kelowna, BC, V1X 4M9

Colors

Designer to choose colors to be used in the design.

Requirements
Must have
• Our logo (attached)

```html
<!DOCTYPE html>
<html lang="en">
<head>
<meta charset="utf-8">
<title>Ridgeline Pet Vision Care – Business Card</title>
<link href="https://fonts.googleapis.com/css2?family=Montserrat:wght@600&family=Oswald:wght@500&family=Roboto:wght@400&display=swap" rel="stylesheet">
<style>
  :root {
    --backdrop: #3a3a3a;
    --card: #2a2a2b;
    --card-deep: #1f1f20;
    --teal: #0d9cab;
    --text: #f1f1f1;
    --muted: #8a8a8a;
    --rule: #6f6f6f;
  }
  * { box-sizing: border-box; margin: 0; padding: 0; }
  html, body { width: 1200px; height: 901px; overflow: hidden; }
  body {
    background: var(--backdrop);
    display: flex;
    flex-direction: column;
    align-items: center;
    justify-content: center;
    gap: 30px;
    font-family: "Roboto", Arial, sans-serif;
  }
  .card {
    position: relative;
    width: 700px;
    height: 400px;
    background: var(--card);
    box-shadow: 0 10px 30px rgba(0,0,0,.45);
    overflow: hidden;
  }
  /* Front side */
  .card-front .pattern-field {
    position: absolute; inset: 0;
    background: linear-gradient(120deg, var(--card-deep) 0%, #262627 50%, #3b3b3c 100%);
  }
  .card-front .brand {
    position: absolute;
    right: 48px; bottom: 110px;
  }
  /* Brand lockup */
  .brand {
    display: flex;
    align-items: center;
    gap: 14px;
  }
  .brand-dot {
    width: 40px; height: 40px;
    border-radius: 50%;
    background: var(--teal);
    flex: none;
  }
  .brand-name {
    font-family: "Montserrat", Arial, sans-serif;
    font-weight: 600;
    color: var(--teal);
    font-size: 22px;
    line-height: 1.15;
    text-transform: uppercase;
    letter-spacing: .04em;
  }
  /* Back side */
  .card-back .brand {
    position: absolute;
    left: 48px; top: 128px;
  }
  .card-back .brand-name { font-size: 19px; }
  .divider {
    position: absolute;
    left: 318px; top: 112px;
    width: 1px; height: 128px;
    background: var(--rule);
  }
  .contact {
    position: absolute;
    left: 338px; top: 112px;
    color: var(--text);
  }
  .person-name {
    font-family: "Oswald", Arial, sans-serif;
    font-weight: 500;
    color: var(--teal);
    font-size: 21px;
    letter-spacing: .02em;
    text-transform: uppercase;
    line-height: 1.1;
  }
  .person-title {
    font-size: 17px;
    margin: 2px 0 14px;
  }
  .contact-list { list-style: none; }
  .contact-list li {
    display: flex; align-items: center; gap: 8px;
    font-size: 15px; line-height: 1.45;
    white-space: nowrap;
  }
  .contact-list svg { width: 13px; height: 13px; flex: none; fill: var(--teal); }
  .web-domain { color: var(--teal); }
  .address {
    position: absolute;
    left: 0; right: 0; top: 318px;
    text-align: center;
    color: var(--text);
    font-size: 17px;
  }
  .accent-band {
    position: absolute;
    left: 0; right: 0; bottom: 0;
    height: 12px;
    background: var(--teal);
  }
</style>
</head>
<body>
  <section class="card card-front" aria-label="Card front">
    <div class="pattern-field" role="img" aria-label="Embossed repeating pattern of the clinic emblem"></div>
    <div class="brand">
      <span class="brand-dot"></span>
      <p class="brand-name">Ridgeline<br>Pet Vision Care</p>
    </div>
  </section>

  <section class="card card-back" aria-label="Card back">
    <div class="brand">
      <span class="brand-dot"></span>
      <p class="brand-name">Ridgeline<br>Pet Vision Care</p>
    </div>
    <span class="divider"></span>
    <div class="contact">
      <h1 class="person-name">Delia Vossman, BSc, DVM, MSc, DipACVO</h1>
      <p class="person-title">Veterinary Ophthalmologist</p>
      <ul class="contact-list">
        <li>
          <svg viewBox="0 0 24 24" aria-hidden="true"><path d="M6.6 10.8a15.5 15.5 0 0 0 6.6 6.6l2.2-2.2a1 1 0 0 1 1-.25 11.4 11.4 0 0 0 3.6.57 1 1 0 0 1 1 1V20a1 1 0 0 1-1 1A17 17 0 0 1 3 4a1 1 0 0 1 1-1h3.5a1 1 0 0 1 1 1c0 1.25.2 2.45.57 3.57a1 1 0 0 1-.25 1z"/></svg>
          250.418.3927
        </li>
        <li>
          <svg viewBox="0 0 24 24" aria-hidden="true"><path d="M2 5h20v14H2z M2 5l10 8 10-8" /></svg>
          ridgelinepetvisioncare@mailbox-example.net
        </li>
        <li>
          <svg viewBox="0 0 24 24" aria-hidden="true"><circle cx="12" cy="12" r="10"/></svg>
          <span>www.<span class="web-domain">ridgelinepetvisioncare-example</span>.net</span>
        </li>
      </ul>
    </div>
    <p class="address">1874 Thornbury Rd, Kelowna, BC, V1X 4M9</p>
    <span class="accent-band"></span>
  </section>
</body>
</html>
```